Marwick Family Chiropractic Stationary

The letterhead and business card must have our logo.
We would like to see the logo used in different ways ( It can be expanded upon in the stationary.)
Please use the the same or similar colors.
Must be eye catching and memorable.
Must be easy to read

Reason: The doctor has been too busy to make any final decisions. He would like to give himself a little more time.

Target Market(s)

Chiropractic Healthcare

Industry/Entity Type

Business

Requirements
Must have
• Dr. Leonard Marwick D.C.
Chiropractor

860-555-0183

417 Birchfield Road, 2nd Floor
Hollisford, NH 06091

drmarwick@marwickspine.example
www.marwickspine.example
www.facebook.com/MarwickFamilySpine
Should not have
• should not be difficult to read

```html
<!DOCTYPE html>
<html lang="en">
<head>
<meta charset="utf-8">
<title>Marwick Family Chiropractic – Business Cards</title>
<link rel="stylesheet" href="https://fonts.googleapis.com/css2?family=Questrial&family=PT+Sans:wght@400;700&display=swap">
<style>
  :root {
    --backdrop: #a3a3a5;
    --card-black: #000000;
    --leaf-green: #a8cf5b;
    --deep-green: #4fae3a;
    --lime-rule: #c9dd3c;
    --taupe: #847461;
    --text-light: #ffffff;
    --divider: #6e6e6e;
    --social-blue: #3b5998;
  }
  * { box-sizing: border-box; margin: 0; padding: 0; }
  html, body { width: 1200px; height: 740px; overflow: hidden; }
  body {
    position: relative;
    background: var(--backdrop);
    font-family: "PT Sans", Arial, sans-serif;
  }
  .card {
    position: absolute;
    width: 556px;
    height: 318px;
    overflow: hidden;
  }
  .card--front    { left: 28px;  top: 30px;  background: var(--card-black); }
  .card--wordmark { left: 613px; top: 30px;  background: var(--card-black); }
  .card--taupe    { left: 28px;  top: 385px; background: var(--taupe); }
  .card--green    { left: 613px; top: 385px; background: var(--leaf-green); }

  .web {
    position: absolute;
    left: 0; right: 0;
    text-align: center;
    font-family: "Questrial", Arial, sans-serif;
    font-size: 15px;
    letter-spacing: 2.4px;
    color: var(--text-light);
  }

  .brand-name {
    font-family: "Questrial", Arial, sans-serif;
    text-align: center;
    color: var(--leaf-green);
    text-transform: uppercase;
    letter-spacing: 1px;
  }

  /* Front card */
  .front__brand {
    position: absolute;
    left: 30px; top: 40px;
    width: 240px; height: 220px;
    display: flex; flex-direction: column;
    align-items: center; justify-content: center;
    gap: 16px;
  }
  .front__brand-dot {
    width: 110px; height: 110px; border-radius: 50%;
    background: var(--leaf-green);
  }
  .front__brand .brand-name { font-size: 17px; line-height: 1.3; }
  .front__divider {
    position: absolute;
    left: 282px; top: 55px;
    width: 1px; height: 185px;
    background: linear-gradient(to bottom, transparent, var(--divider) 15%, var(--divider) 85%, transparent);
  }
  .front__details {
    position: absolute;
    left: 307px; top: 58px;
    color: var(--text-light);
    font-size: 14px;
    line-height: 1.55;
  }
  .front__name  { color: var(--leaf-green); font-size: 17px; font-weight: 700; }
  .front__title { color: var(--deep-green); font-size: 15px; margin-bottom: 14px; }
  .front__address { margin-bottom: 14px; }
  .contact-line { display: flex; align-items: center; gap: 6px; }
  .contact-line svg { flex: none; }
  .social-square { width: 10px; height: 10px; background: var(--social-blue); flex: none; }
  .front__rule {
    position: absolute; left: 0; right: 0; top: 275px;
    height: 2px; background: var(--lime-rule);
  }
  .front__band {
    position: absolute; left: 0; right: 0; top: 279px; bottom: 0;
    background: var(--taupe);
  }
  .card--front .web { top: 287px; }

  /* Wordmark card */
  .wordmark__ghost {
    position: absolute;
    left: 178px; top: 20px;
    width: 200px; height: 250px;
    border-radius: 100px 100px 12px 12px;
    background: radial-gradient(ellipse at 50% 40%, #1e2a1a, #0b0d0a 75%);
  }
  .wordmark__text {
    position: absolute; left: 0; right: 0; top: 88px;
    text-align: center;
  }
  .wordmark__text .brand-name { font-size: 34px; line-height: 1.35; letter-spacing: 2px; }
  .card--wordmark .web { top: 258px; }

  /* Back cards */
  .back__brand {
    position: absolute; left: 0; right: 0; top: 50px;
    display: flex; flex-direction: column; align-items: center; gap: 18px;
  }
  .back__brand-dot { width: 130px; height: 130px; border-radius: 50%; background: var(--text-light); }
  .back__brand .brand-name { color: var(--text-light); font-size: 20px; }
  .card--taupe .web, .card--green .web { top: 260px; }
</style>
</head>
<body>

  <section class="card card--front" aria-label="Business card front">
    <div class="front__brand">
      <span class="front__brand-dot"></span>
      <p class="brand-name">Marwick<br>Family Chiropractic</p>
    </div>
    <div class="front__divider"></div>
    <div class="front__details">
      <p class="front__name">Dr. Leonard Marwick D.C.</p>
      <p class="front__title">Chiropractor</p>
      <p class="front__address">417 Birchfield Road<br>Suite 2B, Hollisford, NH 06091</p>
      <p class="contact-line">
        <svg width="11" height="11" viewBox="0 0 12 12" aria-hidden="true"><circle cx="6" cy="6" r="5.5" fill="none" stroke="#a8cf5b"/><path d="M4 3.5l1 1-0.6 1c.4.8 1 1.4 1.8 1.8l1-.6 1 1-.8 1C5.8 9 3 6.2 3 4.3z" fill="#a8cf5b"/></svg>
        860-555-0183
      </p>
      <p class="contact-line">
        <svg width="11" height="11" viewBox="0 0 12 12" aria-hidden="true"><rect x="1" y="3" width="10" height="7" fill="#a8cf5b"/><path d="M1 3l5 4 5-4" fill="none" stroke="#000" stroke-width="0.8"/></svg>
        mymarwick@marwickspine.example
      </p>
      <p class="contact-line"><span class="social-square"></span>MarwickFamilySpine</p>
    </div>
    <div class="front__rule"></div>
    <div class="front__band"></div>
    <p class="web">www.marwickspine.example</p>
  </section>

  <section class="card card--wordmark" aria-label="Business card back, wordmark">
    <div class="wordmark__ghost" role="img" aria-label="Faint tree emblem in the background"></div>
    <div class="wordmark__text">
      <p class="brand-name">Marwick<br>Family Chiropractic</p>
    </div>
    <p class="web">www.marwickspine.example</p>
  </section>

  <section class="card card--taupe" aria-label="Business card back, taupe">
    <div class="back__brand">
      <span class="back__brand-dot"></span>
      <p class="brand-name">Marwick Family Chiropractic</p>
    </div>
    <p class="web">www.marwickspine.example</p>
  </section>

  <section class="card card--green" aria-label="Business card back, green">
    <div class="back__brand">
      <span class="back__brand-dot"></span>
      <p class="brand-name">Marwick Family Chiropractic</p>
    </div>
    <p class="web">www.marwickspine.example</p>
  </section>

</body>
</html>
```